New website for concierge mobile medical service

new website for business:
WEBSITE REQUEST LIST:
Luxury product look.
Professional. Clean & simple, NO stock people photos. Graphics OK.
Black and white text.

```html
<!DOCTYPE html>
<html lang="en">
<head>
<meta charset="utf-8">
<title>Why Vela Health?</title>
<link href="https://fonts.googleapis.com/css2?family=Lato:ital,wght@0,400;0,700;0,900;1,900&display=swap" rel="stylesheet">
<style>
:root{
  --ink:#111820;
  --violet:#5b5ba6;
  --nav-line:#0d2c3c;
  --hero-dark:#03121c;
  --hero-blue:#0a3e5c;
  --card-top:#3d56a7;
  --card-bottom:#8b79b9;
  --teal:#1a8aa6;
  --teal-dark:#156f8f;
  --button:#86cfd6;
  --field-line:#cfcfcf;
  --footer:#111111;
  --white:#ffffff;
}
*{box-sizing:border-box;margin:0;padding:0}
html,body{width:1200px;height:2400px;overflow:hidden}
body{position:relative;background:var(--white);font-family:'Lato',sans-serif;color:var(--ink)}
.abs{position:absolute}

/* header */
.site-header{left:0;top:0;width:1200px;height:107px;background:var(--white)}
.brand{left:158px;top:18px;width:122px;height:122px;border-radius:50%;background:var(--white);display:flex;align-items:center;justify-content:center;z-index:3}
.brand-mark{width:104px;height:104px;border-radius:50%;background:#0b1f2e;border:5px solid #4fb6c8;display:flex;align-items:center;justify-content:center;color:var(--white);font-weight:700;font-size:17px}
.phone{right:143px;top:16px;display:flex;align-items:center;gap:12px;color:var(--violet);font-weight:700;font-size:19px}
.phone-icon{width:32px;height:32px;background:var(--violet);border-radius:3px;display:flex;align-items:center;justify-content:center}
.main-nav{right:143px;top:75px;display:flex;gap:39px;font-size:13px;font-weight:700;text-transform:uppercase}
.main-nav a{color:var(--ink);text-decoration:none;position:relative}
.main-nav a.active{color:#2a3860}
.main-nav a.active::after{content:"";position:absolute;left:-12px;right:-12px;top:24px;height:5px;background:var(--nav-line)}

/* hero */
.hero{left:0;top:107px;width:1200px;height:265px;background:linear-gradient(100deg,var(--hero-dark) 0%,#061f2e 45%,var(--hero-blue) 100%)}
.hero h1{left:144px;top:104px;font-size:46px;font-weight:900;color:var(--white)}
.hero-art{left:866px;top:31px;width:204px;height:204px;border-radius:50%;border:4px solid #6fd0d6;background:radial-gradient(circle,#0c4a6e 0%,#083650 100%)}

/* cards */
.feature{width:287px;background:linear-gradient(180deg,var(--card-top) 0%,var(--card-bottom) 100%);color:var(--white);text-align:center;padding:30px 14px 0;overflow:hidden}
.feature svg{display:block;margin:0 auto 18px}
.feature h2{font-size:19px;font-weight:700;line-height:24px;margin-bottom:6px}
.feature p{font-size:14px;line-height:24.5px}
.feature .num{position:absolute;right:4px;bottom:-14px;font-size:98px;font-weight:900;font-style:italic;color:rgba(255,255,255,.16);line-height:1}

/* subscribe */
.subscribe{left:0;top:1590px;width:1200px;height:253px;background:linear-gradient(120deg,var(--teal) 0%,var(--teal-dark) 55%,var(--teal) 100%)}
.subscribe h2{left:0;width:1200px;top:42px;text-align:center;font-size:34px;font-weight:700;color:var(--white)}
.field{background:var(--white);font-size:13px;color:#333;padding:0 15px;display:flex;align-items:center}
.btn{background:var(--button);color:var(--white);font-size:16px;font-weight:700;display:flex;align-items:center;justify-content:center;text-transform:uppercase}

/* contact */
.contact-title{left:0;width:1200px;top:1874px;text-align:center;font-size:34px;font-weight:700}
.contact-lead{left:0;width:1200px;top:1927px;text-align:center;font-size:16.5px}
.contact .field{border:2px solid var(--field-line)}

/* footer */
.site-footer{left:0;top:2267px;width:1200px;height:133px;background:var(--footer);color:var(--white)}
.foot-nav{left:0;width:1200px;top:22px;display:flex;justify-content:center;gap:39px;font-size:13px;font-weight:700}
.copyright{left:0;width:1200px;top:58px;text-align:center;font-size:11px}
.social{left:0;width:1200px;top:88px;display:flex;justify-content:center;gap:16px}
.social span{width:18px;height:18px;border-radius:50%;background:var(--white)}
</style>
</head>
<body>

<header class="site-header abs">
  <div class="brand abs"><div class="brand-mark">Vela Health</div></div>
  <div class="phone abs">
    <span class="phone-icon"><svg width="16" height="16" viewBox="0 0 24 24"><path fill="#fff" d="M6.6 10.8a15.1 15.1 0 0 0 6.6 6.6l2.2-2.2c.3-.3.7-.4 1-.2 1.1.4 2.3.6 3.6.6.6 0 1 .4 1 1V20c0 .6-.4 1-1 1A17 17 0 0 1 3 4c0-.6.4-1 1-1h3.5c.6 0 1 .4 1 1 0 1.3.2 2.5.6 3.6.1.3 0 .7-.2 1z"/></svg></span>
    555-010-0199
  </div>
  <nav class="main-nav abs">
    <a href="#">Home</a><a href="#">About Us</a><a href="#" class="active">Why Vela?</a><a href="#">Service Area</a><a href="#">Other</a><a href="#">FAQ</a><a href="#">Contact Us</a>
  </nav>
</header>

<section class="hero abs">
  <h1 class="abs">Why Vela Health?</h1>
  <div class="hero-art abs" role="img" aria-label="Illustration of a medical car with a caduceus inside a glowing ring"></div>
</section>

<!-- features -->
<article class="feature abs" style="left:144px;top:408px;height:343px">
  <svg width="62" height="66" viewBox="0 0 62 66"><circle cx="31" cy="16" r="14" fill="#fff"/><path d="M4 64v-14c0-10 10-16 27-16s27 6 27 16v14z" fill="#fff"/><circle cx="18" cy="52" r="5" fill="#4a5aa8"/><path d="M38 58v-8a6 6 0 0 1 12 0v8" stroke="#4a5aa8" stroke-width="3" fill="none"/></svg>
  <h2>No drive to the doctor when you’re sick ...</h2>
  <p>The last thing you want to do when you don’t feel good is make the trip to the doctor’s office. We come to you in the comfort of your own home or office.</p>
  <span class="num">1</span>
</article>
<article class="feature abs" style="left:457px;top:408px;height:343px">
  <svg width="62" height="66" viewBox="0 0 62 66"><circle cx="31" cy="33" r="16" fill="#fff"/><g stroke="#fff" stroke-width="3"><line x1="31" y1="4" x2="31" y2="62"/><line x1="2" y1="33" x2="60" y2="33"/><line x1="10" y1="12" x2="52" y2="54"/><line x1="52" y1="12" x2="10" y2="54"/></g><circle cx="26" cy="29" r="3" fill="#4a5aa8"/><circle cx="36" cy="37" r="3" fill="#4a5aa8"/></svg>
  <h2>Forget crowded waiting rooms filled with germs ...</h2>
  <p>We provide all of your care in your home or office , clean and easy.</p>
  <span class="num">2</span>
</article>
<article class="feature abs" style="left:771px;top:408px;height:343px">
  <svg width="62" height="66" viewBox="0 0 62 66"><rect x="8" y="14" width="46" height="50" fill="#fff"/><rect x="20" y="2" width="22" height="16" fill="#fff"/><path d="M26 5v10M36 5v10M26 10h10" stroke="#4a5aa8" stroke-width="3"/><g fill="#4a5aa8"><rect x="15" y="24" width="6" height="6"/><rect x="28" y="24" width="6" height="6"/><rect x="41" y="24" width="6" height="6"/><rect x="15" y="36" width="6" height="6"/><rect x="28" y="36" width="6" height="6"/><rect x="41" y="36" width="6" height="6"/><rect x="26" y="50" width="10" height="14"/></g></svg>
  <h2>Skip the trip to the ER or urgent care...</h2>
  <p>We come to you and deliver high level care. Our team has extensive experience in primary care and the emergency room so we’re prepared to handle most medical issues.</p>
  <span class="num">3</span>
</article>

<article class="feature abs" style="left:144px;top:777px;height:380px">
  <svg width="66" height="66" viewBox="0 0 66 66"><circle cx="33" cy="33" r="28" fill="none" stroke="#fff" stroke-width="8"/><path d="M33 17v17H22" stroke="#fff" stroke-width="6" fill="none"/></svg>
  <h2>Avoid the 4 hour<br>wait...</h2>
  <p>We can be at most folks’ home within an hour of request, or, better yet, for non-urgent situations, schedule at your convenience when you would like us to care for you.</p>
  <span class="num">4</span>
</article>
<article class="feature abs" style="left:457px;top:777px;height:380px">
  <svg width="62" height="66" viewBox="0 0 62 66"><path d="M8 2h32l14 14v48H8z" fill="#fff"/><path d="M40 2v14h14" fill="#c8cdea"/><g stroke="#4a5aa8" stroke-width="3"><line x1="18" y1="34" x2="44" y2="34"/><line x1="18" y1="42" x2="44" y2="42"/><line x1="18" y1="50" x2="44" y2="50"/></g></svg>
  <h2>No more 5 pages of<br>forms...</h2>
  <p>We do all the paperwork for you and keep it on file for next<br>time.</p>
  <span class="num">5</span>
</article>
<article class="feature abs" style="left:771px;top:777px;height:380px">
  <svg width="66" height="66" viewBox="0 0 66 66"><circle cx="15" cy="16" r="9" fill="#fff"/><circle cx="51" cy="16" r="9" fill="#fff"/><circle cx="33" cy="24" r="12" fill="#fff"/><path d="M2 46c0-10 6-14 13-14s13 4 13 14zM38 46c0-10 6-14 13-14s13 4 13 14z" fill="#fff"/><path d="M15 64v-12c0-10 8-14 18-14s18 4 18 14v12z" fill="#fff"/></svg>
  <h2>Know your doctor and<br>care team!</h2>
  <p>You will see familiar faces who know your health history. We are physicians and clinicians who are experienced in primary, urgent and emergency care. We go way beyond sick visits and can handle most urgent and emergent situations so that you do not have to leave your home.</p>
  <span class="num">6</span>
</article>

<article class="feature abs" style="left:144px;top:1206px;height:343px">
  <svg width="70" height="70" viewBox="0 0 70 70"><circle cx="22" cy="20" r="18" fill="none" stroke="#fff" stroke-width="3"/><path d="M22 9v12h9" stroke="#fff" stroke-width="3" fill="none"/><circle cx="46" cy="32" r="10" fill="#fff"/><path d="M20 70v-12c0-9 10-14 26-14s26 5 26 14v12z" fill="#fff"/></svg>
  <h2>We’re available for<br>extended hours...</h2>
  <p>hours...Doesn’t it seem that we always need a doctor on Friday night or the weekend? We are available 24 hours, 7 days a week.</p>
  <span class="num">7</span>
</article>

<section class="subscribe abs" role="img" aria-label="Subscribe band with a soft medical pattern background">
  <h2 class="abs">Subscribe</h2>
  <div class="field abs" style="left:276px;top:103px;width:318px;height:44px">Enter Name</div>
  <div class="field abs" style="left:607px;top:103px;width:318px;height:44px">Enter Email Address</div>
  <div class="btn abs" style="left:276px;top:157px;width:649px;height:43px">Subscribe Now</div>
</section>

<section class="contact">
  <h2 class="contact-title abs">Contact Us</h2>
  <p class="contact-lead abs">We want to hear from you! Click below to send us a message and receive upcoming information.</p>
  <div class="field abs" style="left:223px;top:1967px;width:365px;height:41px">Enter Name</div>
  <div class="field abs" style="left:612px;top:1967px;width:366px;height:41px">Enter Email Address</div>
  <div class="field abs" style="left:223px;top:2019px;width:365px;height:41px">Phone No</div>
  <div class="field abs" style="left:612px;top:2019px;width:366px;height:41px">Subject</div>
  <div class="field abs" style="left:223px;top:2070px;width:755px;height:100px;align-items:flex-start;padding-top:16px">Message</div>
  <div class="btn abs" style="left:276px;top:2188px;width:649px;height:43px">Submit Now</div>
</section>

<footer class="site-footer abs">
  <nav class="foot-nav abs"><span>HOME</span><span>ABOUT US</span><span>WHY VELA?</span><span>SERVICE AREA</span><span>OTHER</span><span>CONTACT US</span></nav>
  <p class="copyright abs">Copyright © 2019. Company Name All Rights Reserved</p>
  <div class="social abs" aria-label="Social links"><span></span><span></span><span></span><span></span><span></span></div>
</footer>

</body>
</html>
```